Business card design for Virtual Assistance company

I need a business card designed for my virtual assistance company. We are a small company who services primarily C-level executive clients. The card needs to be double sided with the following contact information on the back:
Melissa Thornbury
Owner/CEO
info@rkpadvisory.net
www.rkpadvisory.net
555.302.9817

The front side should just have the company name incorporated: "RKP Advisory" and "virtual assistance"

The card should be simplistic, but eye catching and should speak to high level executives. Our primary focus areas consist of executive assistance and government contracting.

Target Market(s)

CEOs and executives

Contact Information for Business Card

see project description. phone, email, website.

Colors

Designer to choose only greyscale colors for use in the design.

```html
<!DOCTYPE html>
<html lang="en">
<head>
<meta charset="utf-8">
<title>RKP Advisory – Business Card</title>
<link href="https://fonts.googleapis.com/css2?family=Crimson+Text:wght@400;600;700&family=Montserrat:wght@400&display=swap" rel="stylesheet">
<style>
  :root {
    --backdrop: #8a8580;
    --card: #1c1c1c;
    --ink: #ffffff;
    --ink-soft: #e6e6e6;
  }
  html, body {
    margin: 0;
    padding: 0;
    width: 900px;
    height: 1200px;
    overflow: hidden;
    background: var(--backdrop);
  }
  .canvas {
    position: relative;
    width: 900px;
    height: 1200px;
  }
  .card {
    position: absolute;
    left: 80px;
    width: 742px;
    height: 441px;
    background: var(--card);
    border-radius: 24px;
    color: var(--ink);
    overflow: hidden;
  }
  .card--front { top: 131px; }
  .card--back  { top: 638px; }

  .company-name {
    position: absolute;
    left: 41px;
    top: 68px;
    margin: 0;
    font-family: "Crimson Text", serif;
    font-weight: 600;
    font-size: 47px;
    line-height: 1;
    letter-spacing: -0.3px;
  }
  .person-name {
    position: absolute;
    left: 41px;
    top: 197px;
    margin: 0;
    font-family: "Crimson Text", serif;
    font-weight: 700;
    font-size: 27px;
    line-height: 1;
  }
  .person-role {
    position: absolute;
    left: 41px;
    top: 232px;
    margin: 0;
    font-family: "Montserrat", sans-serif;
    font-size: 16px;
    color: var(--ink-soft);
  }
  .contact-list {
    position: absolute;
    left: 43px;
    top: 290px;
    margin: 0;
    padding: 0;
    list-style: none;
    font-family: "Montserrat", sans-serif;
    font-size: 16px;
    color: var(--ink-soft);
  }
  .contact-list li {
    display: flex;
    align-items: center;
    height: 28px;
  }
  .contact-list svg {
    width: 15px;
    height: 15px;
    margin-right: 10px;
    fill: var(--ink);
  }
  .tagline {
    position: absolute;
    left: 43px;
    top: 391px;
    margin: 0;
    font-family: "Crimson Text", serif;
    font-size: 17px;
    letter-spacing: 0.3px;
    text-transform: uppercase;
  }
  .brand-mark {
    position: absolute;
    font-family: "Crimson Text", serif;
    font-weight: 400;
    color: var(--ink);
    line-height: 0.95;
    margin: 0;
  }
  .brand-mark--front {
    right: 34px;
    top: 150px;
    width: 320px;
    text-align: right;
    font-size: 68px;
  }
  .brand-mark--back {
    left: 0;
    right: 0;
    top: 170px;
    text-align: center;
    font-size: 84px;
  }
</style>
</head>
<body>
<div class="canvas">

  <section class="card card--front">
    <h1 class="company-name">RKP Advisory</h1>
    <h2 class="person-name">Melissa Thornbury</h2>
    <p class="person-role">Owner/CEO</p>
    <ul class="contact-list">
      <li>
        <svg viewBox="0 0 24 24" aria-hidden="true"><path d="M6.6 10.8a15.1 15.1 0 0 0 6.6 6.6l2.2-2.2a1 1 0 0 1 1-.25 11.4 11.4 0 0 0 3.6.57 1 1 0 0 1 1 1V20a1 1 0 0 1-1 1A17 17 0 0 1 3 4a1 1 0 0 1 1-1h3.5a1 1 0 0 1 1 1c0 1.25.2 2.45.57 3.57a1 1 0 0 1-.25 1z"/></svg>
        555.302.9817
      </li>
      <li>
        <svg viewBox="0 0 24 24" aria-hidden="true"><path d="M2 5h20v2l-10 6L2 7z M2 9l10 6 10-6v10H2z"/></svg>
        info@rkpadvisory.net
      </li>
      <li>
        <svg viewBox="0 0 24 24" aria-hidden="true"><path d="M12 2a10 10 0 1 0 0 20 10 10 0 0 0 0-20zm-1 17.9A8 8 0 0 1 4.1 10.9L9 16v1a2 2 0 0 0 2 2zm6.9-2.5A2 2 0 0 0 16 16h-1v-3a1 1 0 0 0-1-1H8v-2h2a1 1 0 0 0 1-1V7h2a2 2 0 0 0 2-2v-.4a8 8 0 0 1 2.9 12.8z"/></svg>
        www.rkpadvisory.net
      </li>
    </ul>
    <p class="tagline">Virtual Assistance</p>
    <p class="brand-mark brand-mark--front">RKP Advisory</p>
  </section>

  <section class="card card--back">
    <p class="brand-mark brand-mark--back">RKP Advisory</p>
  </section>

</div>
</body>
</html>
```